Redesign a Start-Up Dating Website

Website: https://morvelique.com.
Make sure the design has an island style theme.
I would like the 7 pages of my website to have a new and professional look. I want the same colors to remain, but I want a creative look for all the pages. This is a dating website that is in the startup stage. So, I want to give my entire website a custom makeover. I want something that will stand out from the other dating sites. Something that will attract more people to want to use my services, and hopefully get new members.
Target Market(s)
Dating
Industry/Entity Type
Dating
Coding
Coded - Design and coding required
Number of Pages Required
5+ page
Font styles to use
Other font styles liked:
- Decorative, San Serif
Requirements
Must have
- The design must have the original colors and a stylish font to go along. The design must be creative, welcoming, and professional. I would like an island style theme for the website. This is a dating website so make sure that the design is tailored to that aspect.
Nice to have
- It would be nice to have a decorative font and a professional style on all the pages. Make sure the design will be mobile responsive and friendly for all the pages on the website.
Should not have
- The design should not be bland and uncreative.

```html
<!DOCTYPE html>
<html lang="en">
<head>
<meta charset="utf-8">
<title>Morvelique — Premium</title>
<link rel="stylesheet" href="https://fonts.googleapis.com/css2?family=Open+Sans:wght@400;600;700&family=Raleway:wght@600;700&display=swap">
<style>
:root{
  --orange:#f7931e;
  --teal:#4fb3a9;
  --green:#5fb98a;
  --ink:#222;
  --text:#444;
  --muted:#555;
  --line:#9a9a9a;
  --footer-bg:#ededed;
  --white:#fff;
}
*{box-sizing:border-box;margin:0;padding:0}
html,body{width:832px;height:1200px;overflow:hidden;background:var(--white)}
body{position:relative;font-family:"Open Sans",Arial,sans-serif;color:var(--text)}
.accent-line{position:absolute;left:0;width:832px;height:3px;background:linear-gradient(90deg,var(--teal),#9ab06a 50%,var(--orange))}
.site-header{position:absolute;top:0;left:0;width:832px;height:64px;box-shadow:0 1px 3px rgba(0,0,0,.15);background:var(--white);z-index:2}
.brand{position:absolute;left:68px;top:13px;display:flex;align-items:center;gap:8px;font-family:"Raleway",sans-serif;font-weight:700;font-size:24px;color:var(--teal)}
.brand-dot{width:36px;height:36px;border-radius:50%;background:var(--orange)}
.main-nav{position:absolute;left:263px;top:25px;display:flex;gap:18px;font-size:11.5px;font-weight:600;color:var(--ink)}
.main-nav .active{color:var(--orange)}
.login-btn{position:absolute;left:693px;top:17px;width:70px;height:29px;border-radius:15px;background:var(--orange);color:var(--white);font-size:11.5px;font-weight:700;display:flex;align-items:center;justify-content:center;gap:5px}
.hero{position:absolute;top:64px;left:0;width:832px;height:197px;background:linear-gradient(180deg,#6f6a86 0%,#9b8ea3 35%,#c7a8a4 55%,#566a86 75%,#31445f 100%);display:flex;align-items:center;justify-content:center}
.hero h1{font-family:"Open Sans",sans-serif;font-weight:600;font-size:48px;color:var(--white);letter-spacing:1px}
.breadcrumb{position:absolute;left:68px;top:274px;font-size:10.5px;font-weight:600;color:var(--ink)}
.breadcrumb .current{color:var(--orange)}
.rule{position:absolute;left:68px;width:696px;height:1px;background:#c8c8c8}
.intro{position:absolute;left:0;width:832px;text-align:center}
.intro h2{font-size:20px;font-weight:700;color:var(--ink);margin-top:0}
.intro p{font-size:14.5px;color:var(--muted);margin-top:8px}
.intro h3{font-size:17px;font-weight:600;color:var(--text);margin-top:31px}
.card{position:absolute;border:1px solid var(--line);background:var(--white)}
.card-title{font-family:"Raleway",sans-serif;font-weight:600;color:var(--ink);border-bottom:1px solid var(--line);display:flex;align-items:center}
.feature .card-title{height:37px;padding-left:32px;font-size:16.5px}
.feature ul{list-style:none;padding:21px 0 0 32px}
.feature li{display:flex;align-items:center;gap:9px;height:25px;font-size:10.5px;color:var(--text)}
.tick{width:10px;height:10px;flex:none}
.btn{position:absolute;width:91px;height:32px;border-radius:16px;background:var(--orange);color:var(--white);font-size:11.5px;font-weight:700;letter-spacing:.5px;display:flex;align-items:center;justify-content:center}
.feature .btn{left:32px;top:217px}
.plan .card-title{height:36px;padding-left:18px;font-size:15px;font-weight:700;text-transform:uppercase}
.plan-tag{position:absolute;left:16px;top:52px;display:flex;align-items:center;gap:9px;font-size:11px}
.plan-price{position:absolute;left:31px;top:75px;font-size:16px;font-weight:700;color:var(--ink)}
.plan .btn{left:23px;top:110px}
.site-footer{position:absolute;top:1030px;left:0;width:832px;height:170px;background:var(--footer-bg)}
.contact-item{position:absolute;top:30px;display:flex;align-items:center;gap:12px;font-size:9.5px;color:var(--text);line-height:1.5}
.icon-ring{width:30px;height:30px;border:1px solid #aaa;border-radius:50%;display:flex;align-items:center;justify-content:center;flex:none}
.footer-links{position:absolute;top:84px;left:0;width:832px;text-align:center;font-size:10.5px;color:var(--muted);word-spacing:2px}
.copyright{position:absolute;left:70px;top:137px;font-size:9px;color:var(--muted)}
.social{position:absolute;left:679px;top:133px;display:flex;gap:4px}
.social span{width:26px;height:26px;border:1px solid #aaa;border-radius:50%}
</style>
</head>
<body>
<div class="accent-line" style="top:0;z-index:3"></div>
<header class="site-header">
  <div class="brand"><span class="brand-dot"></span>Morvelique</div>
  <nav class="main-nav">
    <span>HOME</span><span>SEARCH</span><span>MEMBERS</span><span>EXTRAS</span><span>ABOUT</span><span class="active">PREMIUM</span><span>CONTACT</span>
  </nav>
  <div class="login-btn">
    <svg width="8" height="9" viewBox="0 0 8 9"><rect x="0.5" y="4" width="7" height="5" rx="1" fill="#fff"/><path d="M2 4V2.7a2 2 0 0 1 4 0V4" fill="none" stroke="#fff" stroke-width="1.2"/></svg>LOGIN
  </div>
</header>

<section class="hero" role="img" aria-label="Couple holding hands on a beach at sunset">
  <h1>PREMIUM</h1>
</section>

<div class="breadcrumb">HOME &nbsp;&gt;&gt;&nbsp; <span class="current">PREMIUM</span></div>
<div class="rule" style="top:299px"></div>

<div class="intro" style="top:350px">
  <h2>PREMIUM MONTHLY PLANS</h2>
  <p>No payment information required with sign-up</p>
  <h3>FEATURES</h3>
</div>

<svg width="0" height="0" style="position:absolute">
  <symbol id="tick" viewBox="0 0 10 10"><circle cx="5" cy="5" r="5" fill="#4fb3a9"/><path d="M2.8 5.1l1.5 1.5 3-3" fill="none" stroke="#fff" stroke-width="1.4"/></symbol>
</svg>

<article class="card feature" style="left:110px;top:489px;width:286px;height:266px">
  <div class="card-title">30-days Free Trial</div>
  <ul>
    <li><svg class="tick"><use href="#tick"/></svg>Advanced &amp; Saved Search</li>
    <li><svg class="tick"><use href="#tick"/></svg>Access &amp; Reply to Email Messages</li>
    <li><svg class="tick"><use href="#tick"/></svg>Compose New Email Messages</li>
    <li><svg class="tick"><use href="#tick"/></svg>Create Albums</li>
    <li><svg class="tick"><use href="#tick"/></svg>Send Winks</li>
    <li><svg class="tick"><use href="#tick"/></svg>Upload Audio/Photos &amp; Videos</li>
  </ul>
  <div class="btn">SIGN UP</div>
</article>

<article class="card feature" style="left:435px;top:489px;width:287px;height:266px">
  <div class="card-title">30-days Free Trial</div>
  <ul>
    <li><svg class="tick"><use href="#tick"/></svg>Comments</li>
    <li><svg class="tick"><use href="#tick"/></svg>Group &amp; One to One Chat</li>
    <li><svg class="tick"><use href="#tick"/></svg>I Viewed &amp; Viewed Me</li>
    <li><svg class="tick"><use href="#tick"/></svg>Instant Messenger &amp; Video Call</li>
    <li><svg class="tick"><use href="#tick"/></svg>Interest Cloud &amp; Virtual Gifts</li>
    <li><svg class="tick"><use href="#tick"/></svg>Zip Code Search</li>
  </ul>
  <div class="btn">SIGN UP</div>
</article>

<article class="card plan" style="left:68px;top:809px;width:214px;height:157px">
  <div class="card-title">$15/3 Months</div>
  <div class="plan-tag"><svg class="tick"><use href="#tick"/></svg>Try it Out</div>
  <div class="plan-price">$15/mo for 3 months</div>
  <div class="btn">SIGN UP</div>
</article>
<article class="card plan" style="left:309px;top:809px;width:214px;height:157px">
  <div class="card-title">$10/6 Months</div>
  <div class="plan-tag"><svg class="tick"><use href="#tick"/></svg>Recommended</div>
  <div class="plan-price">$10/mo for 6 months</div>
  <div class="btn">SIGN UP</div>
</article>
<article class="card plan" style="left:550px;top:809px;width:214px;height:157px">
  <div class="card-title">$5/12 Months</div>
  <div class="plan-tag"><svg class="tick"><use href="#tick"/></svg>Most Popular</div>
  <div class="plan-price">$5/mo for 12 months</div>
  <div class="btn">SIGN UP</div>
</article>

<footer class="site-footer">
  <div class="accent-line" style="top:0"></div>
  <div class="contact-item" style="left:159px">
    <span class="icon-ring"><svg width="9" height="12" viewBox="0 0 9 12"><path d="M4.5 0A4.5 4.5 0 0 0 0 4.5C0 8 4.5 12 4.5 12S9 8 9 4.5A4.5 4.5 0 0 0 4.5 0z" fill="#f7931e"/><circle cx="4.5" cy="4.5" r="1.6" fill="#ededed"/></svg></span>
    <div>Morvelique Dating<br>Contact | Morvelique | Dating Easy</div>
  </div>
  <div class="contact-item" style="left:387px">
    <span class="icon-ring"><svg width="12" height="12" viewBox="0 0 12 12"><path d="M2.4 0.5l2 2.3-1.1 1.5c.8 1.7 2.2 3.1 3.9 3.9l1.5-1.1 2.3 2-1 2.1C5 11 1 7 .4 1.5z" fill="#f7931e"/></svg></span>
    <div>1 800 555 0142</div>
  </div>
  <div class="contact-item" style="left:530px">
    <span class="icon-ring"><svg width="13" height="10" viewBox="0 0 13 10"><rect width="13" height="10" rx="1.5" fill="#f7931e"/><path d="M1 1.5l5.5 4 5.5-4" fill="none" stroke="#ededed" stroke-width="1.2"/></svg></span>
    <div>contact@morvelique.com</div>
  </div>
  <div class="footer-links">Morvelique &nbsp;| &nbsp;About &nbsp;| &nbsp;Contact &nbsp;| &nbsp;Login &nbsp;| &nbsp;Members &nbsp;| &nbsp;Premium &nbsp;| &nbsp;Register &nbsp;| &nbsp;Search</div>
  <div class="rule" style="top:118px"></div>
  <div class="copyright">Copyrights © 2017, Morvelique. All rights reserved.</div>
  <div class="social"><span></span><span></span><span></span></div>
</footer>
</body>
</html>
```